zAvora Corporate Website

zAvora is a well-funded start up developing an Online Marketing Platform for small businesses in Europe.
We are launching in February 2012 with all-in-one online marketing services including professional website, DIY SEO, Dashboard with Reports and Online marketing tools, and Support.
Our internal web designer has come up with a preliminary website design which we wish to continue to improve using new ideas, colours, layout, image, etc.
The brief is very simple - improve the website whether it is look & feel, ease of use, conversion rate - we are looking for overall improvements.
The contest will last 5 days and we will award the winner £300.
If you are the winner , you will also be required to provide designs for 3 more internal pages adhering to the proposed home page design.
Judging criteria : -
Visual Design
Layout must adhere to best practices and wire frame. If you decide to move elements around significantly please provide reason
Functional, informative and drives calls to action
Industry/Entity Type
Marketing
Look and feel
Each slider illustrates characteristics of the customer's brand and the style your logo design should communicate.

```html
<!DOCTYPE html>
<html lang="en">
<head>
<meta charset="utf-8">
<title>zAvora – Online Marketing for Small Business</title>
<link href="https://fonts.googleapis.com/css2?family=Open+Sans:wght@400;600;700&display=swap" rel="stylesheet">
<style>
:root{
  --blue:#1a9fd4;--blue-dark:#1587bb;--blue-light:#3bb4e4;
  --orange:#f07a10;--ink:#333;--grey:#888;
  --dark:#3a3a3a;--darker:#2a2a2a;--beige:#ede8df;
  --olive:#4a3a10;--wine:#5a0e14;--navy:#12175a;
  --green:#7cb82f;--pink:#f0418a;--yellow:#f5d31b;
}
*{margin:0;padding:0;box-sizing:border-box}
html,body{width:816px;height:1200px;overflow:hidden}
body{position:relative;font-family:"Open Sans",Arial,sans-serif;color:var(--ink);background:#fff}
.abs{position:absolute}
.header{left:0;top:0;width:816px;height:44px;background:linear-gradient(#474747,#1d1d1d)}
.logo{left:103px;top:10px;display:flex;align-items:center;gap:5px;color:#fff;font-size:19px;font-weight:600}
.logo .dot{width:17px;height:17px;border-radius:50%;background:var(--blue-light)}
.login{left:654px;top:12px;width:60px;height:22px;border-radius:4px;background:linear-gradient(#fafafa,#d4d4d4);font-size:10px;display:flex;align-items:center;justify-content:center;gap:4px;color:#222}
.login i{width:12px;height:12px;border-radius:50%;background:var(--green)}
.nav{left:0;top:44px;width:816px;height:34px;background:linear-gradient(var(--blue-light),var(--blue))}
.nav a{position:absolute;top:10px;color:#fff;font-size:12px;text-decoration:none}
.nav .active{left:193px;top:-4px;width:52px;height:38px;background:linear-gradient(#fff,#e8eef1);color:#1a5f80;padding-top:14px;text-align:center;border-radius:3px 3px 0 0}
.hero{left:0;top:78px;width:816px;height:252px;background:linear-gradient(#2aa8dc,#1b92c8)}
.hero h1{position:absolute;top:8px;width:816px;text-align:center;color:#fff;font-size:15.5px;font-weight:400;white-space:nowrap}
.hero h1 b{font-weight:700}.hero h1 .sep{color:#8fd3ef;margin:0 6px}
.hero .sub{position:absolute;top:30px;width:816px;text-align:center;color:#d9f1fb;font-size:14px}
.pill{position:absolute;height:20px;background:#fff;border-radius:10px;font-size:9.5px;line-height:20px;color:#222;padding:0 12px;box-shadow:0 1px 2px rgba(0,0,0,.25);white-space:nowrap;overflow:hidden}
.pill.l{text-align:right}
.pill.r{padding:0 8px}
.ring{left:288px;top:130px;width:240px;height:240px;border-radius:50%;background:#1783b6}
.photo{left:303px;top:146px;width:210px;height:210px;border-radius:50%;border:4px solid #fff;background:radial-gradient(circle at 50% 65%,#c79a7c,#6d5a50 45%,#2e2e30 80%)}
.signup{left:331px;top:131px;width:168px;height:31px;border-radius:16px;background:linear-gradient(#a4d250,var(--green));color:#fff;font-size:13px;font-weight:700;padding:6px 0 0 8px;box-shadow:0 2px 3px rgba(0,0,0,.3);white-space:nowrap}
.signup span{position:absolute;right:4px;top:3px;background:linear-gradient(#f15a2a,#c42a10);border-radius:10px;padding:1px 6px;font-size:14px}
.band{left:0;top:330px;width:816px;height:85px;background:linear-gradient(#f7f4ee,var(--beige))}
.band p{position:absolute;width:816px;text-align:center;color:var(--grey);font-size:16px}
.band b{color:var(--orange)}
.section-title{left:0;top:426px;width:816px;text-align:center;color:var(--blue);font-size:16px;font-weight:700}
.client-bar{left:112px;top:454px;width:593px;height:24px;border-top:1px solid #ddd;border-bottom:1px solid #ddd;font-size:8px}
.client-bar .url{position:absolute;left:3px;top:6px}
.client-bar .prev{position:absolute;left:350px;top:6px;color:#555}
.client-bar .next{position:absolute;right:0;top:3px;width:58px;height:16px;background:var(--orange);color:#fff;line-height:16px;text-align:center}
.dots{left:311px;top:485px;display:flex;gap:3px}
.dots i{width:5px;height:5px;border-radius:50%;background:#ccc}.dots i:first-child{background:#999}
.showcase{left:116px;top:498px;width:434px;height:246px;background:linear-gradient(#f4f4f4,#cfd4d8);border-radius:8px}
.blurb{left:511px;top:513px;width:196px;font-size:8.6px;line-height:13.2px;color:#444}
.visit{left:650px;top:719px;font-size:8px;color:#444}
.price{top:757px;width:145px;height:113px;border-radius:4px;color:#fff}
.price .tab{position:absolute;left:4px;top:111px;width:52px;height:16px;background:#222;color:#fff;font-size:9px;font-weight:700;text-align:center;line-height:16px;border-radius:0 0 3px 3px}
.price h3{position:absolute;font-weight:400;line-height:20px;white-space:nowrap}
.price p{position:absolute;font-size:10px;line-height:13px;white-space:nowrap}
.tag{position:absolute;left:4px;top:20px;width:52px;height:92px}
.tag text{font-family:"Open Sans",Arial,sans-serif;font-weight:700}
.how{left:572px;top:758px;width:138px;height:131px;background:#f0ede4;padding:24px 10px 0}
.how .label{position:absolute;left:0;top:-8px;background:var(--yellow);font-size:10px;font-weight:700;color:#5a4a00;padding:3px 7px}
.how p{font-size:10px;font-weight:700;color:#666;line-height:14px}
.features{left:0;top:898px;width:816px;height:108px;background:var(--dark)}
.card{position:absolute;top:5px;width:145px;height:97px;background:linear-gradient(#fff,#d5d5d5);border-radius:3px;text-align:center}
.card h4{margin-top:9px;color:var(--blue);font-size:12px;font-weight:600}
.card p{font-size:7.5px;line-height:10px;padding:2px 8px 0;color:#333}
.card .ico{position:absolute;left:50px;top:49px;width:46px;height:46px;border-radius:4px;background:#fff;box-shadow:0 1px 3px rgba(0,0,0,.4);display:flex;align-items:center;justify-content:center}
.footer{left:0;top:1006px;width:816px;height:91px;background:var(--darker);font-size:7.5px;color:#aaa;line-height:11.5px}
.footer .col{position:absolute;top:15px}
.footer .social{display:flex;gap:4px;margin-top:7px}
.footer .social i{width:17px;height:17px;background:#888;border-radius:2px}
.footer .email{position:absolute;left:539px;top:30px;width:138px;height:16px;background:#1c1c1c;color:#888;padding:2px 5px}
.footer .join{position:absolute;left:678px;top:30px;width:32px;height:16px;background:var(--pink);color:#fff;font-weight:700;text-align:center;padding-top:2px}
.footer .copy{position:absolute;left:620px;top:73px;color:#bbb}
.seo-text{left:105px;top:1100px;width:606px;font-size:6.8px;line-height:9px;color:#333;text-align:center}
.seo-text p{margin-bottom:8px}
</style>
</head>
<body>
<header class="abs header">
  <div class="abs logo"><i class="dot"></i>zAvora</div>
  <div class="abs login"><i></i>LOGIN</div>
</header>
<nav class="abs nav">
  <a class="active">HOME</a><a style="left:272px">QUICK TOUR</a><a style="left:375px">PRICING</a><a style="left:455px">ABOUT US</a><a style="left:547px">CONTACT US</a>
</nav>
<section class="abs hero">
  <h1><b>Business</b> Websites<span class="sep">|</span><b>Online</b> Marketing<span class="sep">|</span><b>Dashboard</b> Controls<span class="sep">|</span><b>Full Setup</b> &amp; Support</h1>
  <p class="sub">Getting a website has never been so simple</p>
</section>
<div class="abs ring"></div>
<div class="abs photo" role="img" aria-label="Photo of a thoughtful man looking up at chalk-drawn arrows on a dark board"></div>
<div class="pill l" style="left:204px;top:140px;width:110px">Testimonials</div>
<div class="pill l" style="left:197px;top:164px;width:108px">Email Marketing</div>
<div class="pill l" style="left:190px;top:188px;width:104px">Hosting</div>
<div class="pill l" style="left:185px;top:213px;width:100px">PPC</div>
<div class="pill l" style="left:183px;top:237px;width:100px">Deals</div>
<div class="pill l" style="left:185px;top:261px;width:100px">Website Design</div>
<div class="pill l" style="left:197px;top:286px;width:104px">Directories</div>
<div class="pill l" style="left:204px;top:310px;width:108px">Blogs/News</div>
<div class="pill r" style="left:504px;top:140px;width:110px">Content Management</div>
<div class="pill r" style="left:512px;top:164px;width:104px">Reporting</div>
<div class="pill r" style="left:522px;top:188px;width:102px">Socialbook</div>
<div class="pill r" style="left:530px;top:213px;width:102px">Chirper Feeds</div>
<div class="pill r" style="left:532px;top:237px;width:100px">SEO</div>
<div class="pill r" style="left:530px;top:261px;width:100px">Seekly Ads</div>
<div class="pill r" style="left:522px;top:286px;width:102px">Images</div>
<div class="pill r" style="left:512px;top:310px;width:100px">Referrals</div>
<div class="abs signup">Sign up now for <span>FREE!</span></div>
<section class="abs band">
  <p style="top:36px">The Complete <b>Online Marketing Solution</b> for <b>Small Business Websites</b></p>
  <p style="top:58px">"Get a big online presence and more <b>sales leads in 30 minutes</b>"</p>
</section>
<h2 class="abs section-title">View examples of our stunning business websites</h2>
<div class="abs client-bar">
  <span class="url">http://www.sampleclient.com/</span>
  <span class="prev">←&nbsp;&nbsp;&nbsp;previous client</span>
  <span class="next">next client →</span>
</div>
<div class="abs dots"><i></i><i></i><i></i><i></i><i></i></div>
<div class="abs showcase" role="img" aria-label="Laptop showing an example client website with a chart on its screen"></div>
<p class="abs blurb">Lorem Ipsum is simply dummy text of the printing and typesetting industry. Lorem Ipsum has been the industry's standard dummy text ever since the 1500s, when an unknown printer took a galley of type and scrambled it to make a type specimen book. It has survived not only five centuries, but also the leap into electronic type-setting, remaining essentially unchanged. It was popularised in the 1960s with the release of Lettrex sheets containing Lorem Ipsum passages, and more recently with desktop pub-lishing software like Quillset Layout including versions of Lorem Ipsum.</p>
<span class="abs visit">visit website →</span>

<div class="abs price" style="left:112px;background:var(--olive)">
  <svg class="tag" viewBox="0 0 52 92"><path d="M8 14 L26 2 L44 14 V90 H8Z" fill="#f2a51a"/><circle cx="26" cy="12" r="3" fill="var(--olive)"/><text x="26" y="42" fill="#222" font-size="13" text-anchor="middle">FREE</text><text x="26" y="62" fill="#fff" font-size="15" text-anchor="middle">£199</text></svg>
  <h3 style="left:66px;top:30px;font-size:24px;color:#e8c64a">Setup</h3>
  <p style="left:69px;top:80px">Web<br>offer only</p>
  <div class="tab">Value</div>
</div>
<div class="abs price" style="left:263px;background:var(--wine)">
  <svg class="tag" viewBox="0 0 52 92"><path d="M8 14 L26 2 L44 14 V90 H8Z" fill="#d8281e"/><circle cx="26" cy="12" r="3" fill="var(--wine)"/><text x="26" y="44" fill="#ffd23a" font-size="9" text-anchor="middle">PRO</text><text x="26" y="55" fill="#ffd23a" font-size="9" text-anchor="middle">PACKAGE</text><text x="26" y="80" fill="#fff" font-size="17" text-anchor="middle">£22</text></svg>
  <h3 style="left:54px;top:12px;font-size:17px">Big Online<br><span style="color:#f6b6bd">Presence</span></h3>
  <p style="left:65px;top:66px">Business<br>Website &amp;<br>Easy Dashbord</p>
  <div class="tab">Per month</div>
</div>
<div class="abs price" style="left:414px;background:var(--navy)">
  <svg class="tag" viewBox="0 0 52 92"><path d="M8 14 L26 2 L44 14 V90 H8Z" fill="#2a58c8"/><circle cx="26" cy="12" r="3" fill="var(--navy)"/><text x="26" y="38" fill="#fff" font-size="9" text-anchor="middle">TURBO</text><text x="26" y="48" fill="#fff" font-size="9" text-anchor="middle">SALES</text><text x="26" y="58" fill="#fff" font-size="9" text-anchor="middle">PRO PLUS</text><text x="26" y="80" fill="#fff" font-size="17" text-anchor="middle">£22</text></svg>
  <h3 style="left:52px;top:12px;font-size:17px;text-align:center;width:90px">More Sales<br><span style="color:#a9c0ff">Leads</span></h3>
  <p style="left:65px;top:54px">Business<br>Website, Easy<br>Dashboard<br>&amp;PPC Sales</p>
  <div class="tab">Per month</div>
</div>
<aside class="abs how">
  <span class="label">How does it work?</span>
  <p>Neque porro quisquam est qui dolorem ipsum quia dolor sit amet, dolorem ipsum quiaconsectetur, adipisci velit"</p>
</aside>

<section class="abs features">
  <div class="card" style="left:108px"><h4>CASE STUDIES</h4><p>Read real stories abut small business online...</p><div class="ico"><svg width="30" height="20"><rect x="2" y="3" width="26" height="15" rx="2" fill="#666"/><rect x="5" y="6" width="9" height="8" fill="#bbb"/></svg></div></div>
  <div class="card" style="left:259px"><h4>HOW TO</h4><p>Learn from our online marketin tips for small business...</p><div class="ico"><svg width="22" height="32"><circle cx="11" cy="12" r="9" fill="#f6d43a"/><rect x="7" y="21" width="8" height="7" fill="#999"/></svg></div></div>
  <div class="card" style="left:410px"><h4>NEWS &amp; CHATTER</h4><p>Get up to-date news &amp; chatter about online marketing...</p><div class="ico"><svg width="30" height="26"><ellipse cx="12" cy="10" rx="11" ry="8" fill="#7cb82f"/><ellipse cx="19" cy="16" rx="10" ry="7" fill="#e8d8a0"/></svg></div></div>
  <div class="card" style="left:562px"><h4>DEMO</h4><p>Find out what zAvora can do for your business...</p><div class="ico"><svg width="30" height="26"><ellipse cx="15" cy="12" rx="13" ry="10" fill="#3ab2e6"/><path d="M6 20 L4 26 L12 21Z" fill="#3ab2e6"/><rect x="9" y="8" width="9" height="8" fill="#fff"/><path d="M18 12 L23 8 V16Z" fill="#fff"/></svg></div></div>
</section>
<footer class="abs footer">
  <div class="col" style="left:106px">Search Marketing<br>Organic/Natural (SEO)<br>Social Media<br>Web Analytics</div>
  <div class="col" style="left:221px">Concat us<br>Customer Support<br>Request a call back<br>FAQ's</div>
  <div class="col" style="left:325px">Site Map<br>Terms and Conditions</div>
  <div class="col" style="left:437px">Get Social with Us!<div class="social"><i></i><i></i></div></div>
  <div class="col" style="left:539px">Sign up for monthy Newsletter</div>
  <div class="email">Enter your email address</div>
  <div class="join">Join</div>
  <div class="copy">© 2012 zAvora Pvt. Ltd</div>
</footer>
<div class="abs seo-text">
  <p>zAvora will build your business website, optimise SEO marketing and make recommendations on best practices to help you win customers. let our team of experts design a business website for you. Choose a business website from zAvora's broad array of fabulous customisable business websites and our experts will have your business online in minutes. zAvora lets you create a professional business website without the need to know how to code or programme.</p>
  <p>Your business website comes with automatic Internet marketing, marketing on the Internet is easy with zAvora, we automatically optimise your site for SEO marketing and we can run ad campaigns when you need them. Get a business website with online marketing now. zAvora brings your Small Business Website to LIFE!</p>
  <p>View our example business websites above, watch the video demo to see how to make a business website or call us now and get your business marketing online today. The zAvora website builder gives you a professional online appearance - post your own images, give customers your latest news and create customer testimonials, it's the most complete online marketing solution for your business.</p>
</div>
</body>
</html>
```